Envelope design

We need a envelope design for a professional services firm called Brenwick Tax Advisory Inc. The firm is essentially a very specialized tax accounting firm - instead of serving the end consumer, we support other public accounting firms in the area of Canadian and U.S. tax advisory and compliance (i.e. they call us on tax issues too complex for the general practitioner). Our byline is "Tax Support Services for Public Accounting Firms". Our postcard should utilize our logo and be based on colours present in our logo (see file attached). The final design needs to convey professionalism and trustworthiness (we're hired by accountants after all!) while being creative and eye-catching. Eye-catching is critical, since many prospective recipients will not have heard from me before and I want them to read the postcard.
At lot of design work has already been done here. I've attached a number of sample files showing logo and letterhead designs. Please note that the letterhead hasn't yet been updated for the new logo. This is happening in a separate design competition.
Updates
Project Deadline Extended Reason: Deadline is extended because I am pricing the extra cost of having colour right to the edge of the envelopes. This will help me design on final design. Pricing should come in on Monday. Added Saturday, February 20, 2016

```html
<!DOCTYPE html>
<html lang="en">
<head>
<meta charset="utf-8">
<title>Brenwick Tax Advisory Inc. – Envelope</title>
<link rel="stylesheet" href="https://fonts.googleapis.com/css2?family=Cinzel:wght@400;500&family=PT+Sans:wght@400&display=swap">
<style>
  :root {
    --backdrop: #4a3427;
    --band: #111111;
    --paper: #ffffff;
    --edge: #d6d6d6;
    --ink: #222222;
    --brand-white: #f4f4f4;
    --brand-blue: #2f6fb3;
    --pattern-grey: #d2d2d2;
  }
  * { margin: 0; padding: 0; box-sizing: border-box; }
  html, body {
    width: 1200px;
    height: 1000px;
    overflow: hidden;
    background: var(--backdrop);
  }
  .canvas {
    position: relative;
    width: 1200px;
    height: 1000px;
  }
  .envelope {
    position: absolute;
    left: 195px;
    width: 808px;
    height: 350px;
    background: var(--paper);
    border: 1px solid var(--edge);
    box-shadow: 2px 4px 10px rgba(0, 0, 0, 0.35);
    overflow: hidden;
  }
  .envelope--front { top: 148px; }
  .envelope--back { top: 556px; }

  /* Front */
  .brand-band {
    height: 112px;
    background: var(--band);
    display: flex;
    align-items: center;
    justify-content: center;
    gap: 12px;
    padding-right: 14px;
  }
  .brand-mark {
    width: 55px;
    height: 55px;
    background: var(--brand-blue);
    flex: none;
  }
  .brand-words {
    display: flex;
    flex-direction: column;
    align-items: stretch;
    color: var(--brand-white);
    font-family: "Cinzel", serif;
  }
  .brand-name {
    font-size: 37px;
    font-weight: 500;
    line-height: 1;
    letter-spacing: 0.5px;
    white-space: nowrap;
    padding-bottom: 5px;
    border-bottom: 1.5px solid var(--brand-white);
  }
  .brand-tagline {
    font-size: 17px;
    font-weight: 500;
    letter-spacing: 2.7px;
    line-height: 1;
    padding-top: 5px;
    white-space: nowrap;
  }

  /* Back */
  .back-pattern {
    position: absolute;
    inset: 0;
    background: var(--pattern-grey);
  }
  .back-flap {
    position: absolute;
    left: 0;
    top: 0;
    width: 100%;
    height: 126px;
    background: var(--paper);
    border-bottom: 1px solid #bdbdbd;
    border-radius: 0 0 26px 26px;
    box-shadow: 0 1px 3px rgba(0, 0, 0, 0.2);
    text-align: center;
    padding-top: 36px;
    font-family: "PT Sans", sans-serif;
    font-size: 10px;
    line-height: 14px;
    color: var(--ink);
  }
</style>
</head>
<body>
  <main class="canvas">
    <section class="envelope envelope--front" aria-label="Envelope front">
      <header class="brand-band">
        <span class="brand-mark" aria-hidden="true"></span>
        <div class="brand-words">
          <span class="brand-name">BRENWICK TAX ADVISORY</span>
          <span class="brand-tagline">TAX SUPPORT FOR PUBLIC ACCOUNTING FIRMS</span>
        </div>
      </header>
    </section>

    <section class="envelope envelope--back" aria-label="Envelope back">
      <div class="back-pattern" role="img" aria-label="Light grey repeating brand-symbol pattern"></div>
      <div class="back-flap">
        <p class="return-address">18-412 Harlow Crescent, Bedford, Nova Scotia, Canada B4A 2K7</p>
        <p class="return-contact">T: 902.555.0148 &nbsp;|&nbsp; F: 902.555.0172 &nbsp;|&nbsp; E: daniel@brenwicktax.ca</p>
        <p class="return-web">www.brenwicktax.ca</p>
      </div>
    </section>
  </main>
</body>
</html>
```